House-share and Room Rental Website (With Focus on the Bedroom Landing Page)

Looking for website design for our House-share (executive accommodation) and room rental business.

Our company name is: Lodgivo could also be written as LodGivo or lodgivo. Either is fine .. just looking for a nice clean catchy logo to go with the design.

EXAMPLES
These are examples of other websites in this field that are doing well. this is a kind of baseline.
https://nestpartners-example.com.au/
https://www.bunkora-example.com/
https://www.dwelzy-example.com/
https://www.habiquo-example.net/
https://www.cohabiscout-example.com.au/

Our business model is to rent rooms to people looking for high-quality accommodation. We fill the gap between those looking to rent rooms and those with rooms to rent. However, our model is slightly different from those already on the market as we looking to fill a massive gap in the market delivering upmarket rooms for rent.(Executive Accommodation) also in the back end will be coupled with a self management process in the back end.

We offer executive style accommodation that stands out above the rest. With special extras like fire safety.. and management processes that create happier homes. We are looking for a web design package that can help us grow and scale our business. We need a design that is captivating

Our MAIN focus is having a room landing page that stands out from the rest... The core of our business will rely on the promotion of the rooms in a share house... so the whole design relies on the BEDROOM landing page to drive results.

Target Market(s)

We have 2 markets we are aiming at ... the first market is people offering rooms to rent who want the highest rental return. The second market is people looking to rent safe, high-quality rooms, in houses that are well managed and looked after.

Industry/Entity Type

Share Economy

Logo Text

LodGivo

Number of Pages Required

5+ page

Font styles to use
Sans Serif

Colors
3276b5

Requirements
Must have
• A messaging system whereby we can create direct communication between those offering rooms and those looking for rooms.
• A call to action that says " Schedule an Inspection"
• Landing page for promoting rooms
• A home page for showing stock.
• Profile page for those selling rooms
• Profile page for those looking for rooms.
• A scheduling calendar for booking inspections
Nice to have
• Pages where new residents can lock in a room.. pay bond and rents.. and sign contracts
• Notifications
• SMS capabilities in the backend.
Should not have
• No script or handwriting fonts.

```html
<!DOCTYPE html>
<html lang="en">
<head>
<meta charset="utf-8">
<title>Lodgivo – Executive Accommodation for Two</title>
<link rel="stylesheet" href="https://fonts.googleapis.com/css2?family=Questrial&family=Open+Sans:wght@600&display=swap">
<style>
  :root {
    --brand: #3276b5;
    --brand-dark: #1f5da6;
    --brand-deep: #1b4c86;
    --navy: #1c2a6b;
    --ink: #4a4a4a;
    --rule: #cfcfcf;
    --white: #ffffff;
  }
  * { box-sizing: border-box; margin: 0; padding: 0; }
  html, body { width: 714px; height: 1200px; overflow: hidden; background: var(--white); }
  body { position: relative; font-family: "Questrial", sans-serif; color: var(--ink); }
  .abs { position: absolute; }

  .site-header { left: 0; top: 0; width: 714px; height: 72px; }
  .brand { display: flex; align-items: center; gap: 7px; color: var(--brand); font-size: 26px; letter-spacing: 0.5px; }
  .brand-dot { width: 14px; height: 14px; border-radius: 50%; background: var(--brand); }
  .site-header .brand { position: absolute; left: 19px; top: 16px; }
  .header-rule { left: 0; top: 72px; width: 714px; height: 4px; background: var(--brand); }

  .hero { left: 0; top: 76px; width: 714px; height: 405px; overflow: hidden; }
  .hero-photo { position: absolute; inset: 0;
    background: radial-gradient(ellipse at 45% 85%, #6e6e6e 0%, #3f3f3f 30%, #262626 65%, #1a1a1a 100%); }
  .hero-title { position: absolute; left: 0; width: 714px; top: 102px; text-align: center; color: var(--white);
    font-weight: 400; font-size: 25.5px; letter-spacing: 0.3px; }
  .hero-copy { position: absolute; left: 163px; width: 388px; top: 151px; text-align: center; color: var(--white);
    font-family: "Open Sans", sans-serif; font-weight: 600; font-size: 9.6px; line-height: 22.4px; }
  .cta { position: absolute; left: 235px; top: 243px; width: 205px; height: 36px; border-radius: 6px; background: var(--brand);
    color: var(--white); font-size: 15px; display: flex; align-items: center; justify-content: center; }
  .hero-arrow { position: absolute; top: 145px; }

  .facts { left: 0; top: 481px; width: 714px; height: 46px; display: flex; }
  .fact { height: 46px; display: flex; align-items: center; gap: 8px; padding-left: 10px; color: var(--white);
    background: var(--brand-dark); white-space: nowrap; overflow: hidden; }
  .fact:nth-child(even) { background: var(--brand); }
  .fact-label { font-size: 9.6px; text-transform: uppercase; }
  .fact-value { font-size: 12.5px; margin-top: 3px; }

  .panel { top: 559px; width: 243px; height: 205px; border: 2px solid var(--rule); background: var(--white); padding: 17px 0 0 0; z-index: 2; }
  .panel-rooms { left: 94px; }
  .panel-public { left: 381px; }
  .panel h2 { font-weight: 400; font-size: 11.5px; color: var(--navy); text-transform: uppercase; }
  .panel-rooms h2 { padding-left: 52px; margin-bottom: 5px; }
  .panel-public h2 { padding-left: 32px; margin-bottom: 4px; }
  .list { list-style: none; }
  .list li { font-size: 12px; color: var(--brand); height: 22.4px; display: flex; align-items: center; white-space: nowrap; }
  .list li::before { content: "❖"; color: #777; font-size: 9px; width: 14px; margin-right: 14px; text-align: center; }
  .panel-rooms .list li { padding-left: 30px; }
  .panel-public .list li { padding-left: 38px; }
  .panel-public h2.core { padding-left: 27px; margin-top: 3px; font-size: 12px; }
  .core-row { padding-left: 27px; font-size: 10.5px; display: flex; margin-top: 8px; }
  .core-row dt { color: var(--brand); width: 51px; text-transform: uppercase; }
  .core-row dd { color: var(--ink); }

  .bed-photo { left: 320px; top: 745px; width: 394px; height: 320px; z-index: 0;
    background:
      linear-gradient(180deg, rgba(255,255,255,1) 0%, rgba(255,255,255,0) 35%),
      linear-gradient(100deg, rgba(255,255,255,1) 0%, rgba(234,231,227,0.9) 30%, #b9b3aa 55%, #8f887e 75%, #d8d6d2 100%); }
  .map { left: 94px; top: 852px; width: 210px; height: 187px; border: 2px solid var(--brand); z-index: 2;
    background: linear-gradient(135deg, #e9e7df 0%, #dedbd2 50%, #e6e3db 100%); }

  .site-footer { left: 0; top: 1065px; width: 714px; height: 115px; background: var(--brand); border-top: 2px solid var(--brand-dark); color: var(--white); z-index: 3; }
  .contact { position: absolute; left: 12px; top: 18px; }
  .contact h2 { font-weight: 400; font-size: 15px; margin-bottom: 5px; }
  .contact p { font-size: 12px; line-height: 17.5px; }
  .site-footer .brand { position: absolute; left: 200px; top: 30px; color: var(--white); font-size: 50px; gap: 12px; }
  .site-footer .brand-dot { width: 26px; height: 26px; background: var(--white); }
  .quick-links { position: absolute; left: 590px; top: 40px; }
  .quick-links h2 { font-weight: 400; font-size: 14px; margin-bottom: 6px; }
  .quick-links li { list-style: none; font-size: 12px; line-height: 17.5px; padding-left: 4px; }
  .legal-bar { left: 0; top: 1180px; width: 714px; height: 20px; background: var(--brand-deep); color: var(--white); font-size: 9.5px; z-index: 3;
    display: flex; justify-content: space-between; align-items: center; padding: 0 10px 0 12px; }
</style>
</head>
<body>

<header class="site-header abs">
  <div class="brand"><span class="brand-dot"></span>lodgivo</div>
</header>
<div class="header-rule abs"></div>

<section class="hero abs">
  <div class="hero-photo" role="img" aria-label="Dimly lit modern bedroom with a low bed and concrete wall"></div>
  <h1 class="hero-title">EXCEUTIVE ACCOMODATION FOR TWO</h1>
  <p class="hero-copy">Lorem ipsum dolor sit amet, consectetur adipiscing elit, sed do eiusmod tempor incididunt ut labore et dolore magna aliqua. Ut enim ad minim veniam, quis nostrud exercitation commodo consequat</p>
  <a class="cta">Schedule an Inspection</a>
  <svg class="hero-arrow" style="left:18px" width="38" height="50" viewBox="0 0 38 50"><polyline points="36,1 2,25 36,49" fill="none" stroke="#fff" stroke-width="2.5"/></svg>
  <svg class="hero-arrow" style="left:658px" width="38" height="50" viewBox="0 0 38 50"><polyline points="2,1 36,25 2,49" fill="none" stroke="#3d86d6" stroke-width="2.5"/></svg>
</section>

<section class="facts abs">
  <div class="fact" style="width:137px">
    <svg width="32" height="28" viewBox="0 0 32 28" fill="none" stroke="#fff" stroke-width="2"><rect x="5" y="3" width="22" height="16" rx="1"/><path d="M1 24h30"/><circle cx="20" cy="9" r="5"/><path d="M20 9l2-2"/></svg>
    <div><div class="fact-label">Internet Speed</div><div class="fact-value">2 mbps</div></div>
  </div>
  <div class="fact" style="width:121px">
    <svg width="44" height="24" viewBox="0 0 44 24" fill="#fff"><rect x="2" y="2" width="3" height="20"/><rect x="39" y="8" width="3" height="14"/><circle cx="11" cy="10" r="4"/><rect x="5" y="13" width="37" height="5"/><rect x="16" y="8" width="23" height="5" rx="2"/></svg>
    <div><div class="fact-label">Bed Size</div><div class="fact-value">6 by 6</div></div>
  </div>
  <div class="fact" style="width:151px">
    <svg width="30" height="30" viewBox="0 0 30 30" fill="none" stroke="#fff" stroke-width="2.2"><circle cx="11" cy="14" r="6"/><circle cx="17" cy="12" r="6"/><path d="M21 8l6-6M22 2h5v5M11 20v8M8 25h6"/></svg>
    <div><div class="fact-label">Gender Preference</div><div class="fact-value">Couple</div></div>
  </div>
  <div class="fact" style="width:116px">
    <svg width="26" height="32" viewBox="0 0 26 32" fill="none" stroke="#fff" stroke-width="2.2"><path d="M13 24s-8-8-8-13a8 8 0 0116 0c0 5-8 13-8 13z"/><circle cx="13" cy="11" r="3"/><ellipse cx="13" cy="27" rx="11" ry="3"/></svg>
    <div><div class="fact-label">Room Area</div><div class="fact-value">400 sqm</div></div>
  </div>
  <div class="fact" style="width:189px">
    <svg width="32" height="30" viewBox="0 0 32 30" fill="none" stroke="#fff" stroke-width="2"><path d="M4 16V5a3 3 0 016 0"/><path d="M8 7l4 4"/><path d="M2 16h28v4a6 6 0 01-6 6H8a6 6 0 01-6-6z" fill="#fff"/><path d="M7 26l-1 3M25 26l1 3"/></svg>
    <div><div class="fact-label">Bathroom Type</div><div class="fact-value">Shared</div></div>
  </div>
</section>

<section class="panel panel-rooms abs">
  <h2>Room Amenities</h2>
  <ul class="list">
    <li>Furnished/unfurnished</li>
    <li>TV</li>
    <li>Storage space</li>
    <li>Study Desk / Workstation</li>
    <li>Wardrobe</li>
    <li>Ensuite shower</li>
    <li>Kitchenette</li>
  </ul>
</section>

<section class="panel panel-public abs">
  <h2>Public Ammenities</h2>
  <ul class="list">
    <li>Transport options</li>
    <li>Trains</li>
    <li>Busses</li>
    <li>50 miles from Washington DC</li>
  </ul>
  <h2 class="core">Core Infomation</h2>
  <dl>
    <div class="core-row"><dt>Adress</dt><dd>Abc Street, NY Town</dd></div>
    <div class="core-row"><dt>Utilities</dt><dd>Included</dd></div>
  </dl>
</section>

<div class="bed-photo abs" role="img" aria-label="Close-up of a bed with striped grey pillows on white linen"></div>
<div class="map abs" role="img" aria-label="Street map showing the room location and travel routes"></div>

<footer class="site-footer abs">
  <div class="contact">
    <h2>CONTACT US</h2>
    <p>Marlow Street 1234</p>
    <p>NY, Example</p>
    <p>infor@roomvale-example.com</p>
    <p>www.roomvale-example.com</p>
  </div>
  <div class="brand"><span class="brand-dot"></span>lodgivo</div>
  <nav class="quick-links">
    <h2>QUICK LINKS</h2>
    <ul><li>Bedrooms</li><li>Sitting Rooms</li><li>Homes</li></ul>
  </nav>
</footer>
<div class="legal-bar abs"><span>© Roomvale Ltd 2019</span><span>Terms | Privacy Policy</span></div>

</body>
</html>
```